1 Page for Computer Repair Website

Looking for a 1 page website with a design that compliments the business card and pamphlet that have already been made (attached files). It should look business professional and easy to read. Email and phone number should be somewhere near the top of the website, visible when the page loads. I don't want any forms for people to mess with. No "Contact Us" form or entering in email for newsletter. Customers will just be looking at this site to confirm we are professionals and have our business in order.

Target Market(s)

Home and small business

Industry/Entity Type

Computer Repair

Coding

Coded - Design and coding required

Number of Pages Required

1 page

Font styles to use
Other font styles liked:
• Helvetica variations used in pamphlet and card

Colors
0455a3
cfdeed
85abd2
3276b5
85cae6
ffffff

Requirements
Must have
• Compliment the pamphlet and business card in color choices and font use. Pleasing to the eye and easy to read through categories and text.
Should not have
• Forms. No "enter name and email here" or anything of the sort.

```html
<!DOCTYPE html>
<html lang="en">
<head>
<meta charset="utf-8">
<title>ByteWell Computer Services</title>
<link rel="stylesheet" href="https://fonts.googleapis.com/css2?family=Open+Sans:wght@300;400;600&display=swap">
<style>
:root{
  --navy:#0455a3;
  --mid-blue:#3276b5;
  --sky:#85cae6;
  --soft-blue:#85abd2;
  --pale:#cfdeed;
  --white:#ffffff;
  --cyan:#4fc3e8;
  --night:#071a20;
  --panel:#0d2229;
  --teal-dark:#0a2c36;
  --text-grey:#5a6770;
}
*{box-sizing:border-box;margin:0;padding:0}
html,body{width:724px;height:1200px;overflow:hidden}
body{font-family:"Open Sans",Helvetica,Arial,sans-serif;background:var(--night)}
.page{position:relative;width:724px;height:1200px;overflow:hidden}
.backdrop{position:absolute;inset:0;background:linear-gradient(180deg,#0e2e36 0%,#081c22 50%,#0b2a33 100%)}
.panel{position:absolute;left:34px;top:0;width:656px;height:1200px;background:var(--panel)}

/* header */
.site-header{position:absolute;left:0;top:0;width:656px;height:40px}
.brand{position:absolute;left:10px;top:2px;color:var(--white);font-weight:400;line-height:1}
.brand-name{font-size:24px;letter-spacing:.5px;display:block}
.brand-tag{font-size:8px;display:block;margin-top:1px}
.main-nav{position:absolute;right:10px;top:0;display:flex;height:26px}
.main-nav a{color:var(--white);text-decoration:none;font-size:8px;letter-spacing:.4px;padding:0 11px;line-height:26px;position:relative}
.main-nav a.active{background:rgba(255,255,255,.08)}
.main-nav a.active::after{content:"";position:absolute;left:0;right:0;bottom:0;height:2px;background:var(--cyan)}
.contact-strip{position:absolute;right:16px;top:27px;display:flex;gap:18px;font-size:7px;color:var(--white)}
.contact-strip span{display:flex;align-items:center;gap:5px}
.contact-strip svg{width:10px;height:10px}

/* hero */
.hero{position:absolute;left:0;top:42px;width:656px;height:330px;background:linear-gradient(135deg,#c9c8c3 0%,#8c8d8e 40%,#3b3f44 75%,#2a2d31 100%)}
.slide-arrow{position:absolute;top:165px;width:16px;height:22px;background:var(--cyan);display:flex;align-items:center;justify-content:center}
.slide-arrow.prev{left:4px}
.slide-arrow.next{right:4px}
.slide-arrow svg{width:8px;height:10px}
.slide-dots{position:absolute;left:0;right:0;bottom:6px;display:flex;justify-content:center;gap:5px}
.slide-dots i{width:6px;height:6px;border-radius:50%;background:rgba(255,255,255,.45);display:block}
.slide-dots i.on{background:var(--cyan)}

/* services */
.services{position:absolute;left:0;top:372px;width:656px;height:488px;background:radial-gradient(ellipse at 50% 40%,#15414d 0%,var(--teal-dark) 60%,#061a20 100%)}
.section-title{text-align:center;font-weight:300;letter-spacing:1px}
.services .section-title{position:absolute;left:0;right:0;top:26px;color:var(--white);font-size:25px}
.title-rule{position:absolute;left:298px;top:63px;width:60px;height:1px;background:var(--sky)}
.tile{position:absolute;width:104px;height:104px;transform:rotate(45deg);background:var(--white);border:5px solid var(--cyan)}
.tile.photo{background:linear-gradient(135deg,#9a9a96,#3c3f43)}
.service{position:absolute;width:80px;height:66px;display:flex;flex-direction:column;align-items:center;justify-content:center;text-align:center;color:#1a2a33}
.service h3{font-size:7.5px;font-weight:600;color:var(--navy);line-height:1.15;margin-bottom:2px}
.service p{font-size:5.6px;line-height:1.3}
.more{display:inline-block;margin-top:3px;font-size:5px;color:var(--white);background:var(--mid-blue);border-radius:6px;padding:1px 6px}
.view-all{position:absolute;left:293px;top:433px;width:70px;height:22px;border:1px solid var(--white);border-radius:11px;color:var(--white);font-size:8px;line-height:20px;text-align:center}

/* why */
.why{position:absolute;left:0;top:860px;width:656px;height:237px;background:linear-gradient(170deg,#ffffff 0%,#eef1f3 45%,#b9c3c9 100%)}
.why .section-title{position:absolute;left:0;right:0;top:24px;color:var(--mid-blue);font-size:24px}
.why p{position:absolute;left:90px;width:476px;top:72px;text-align:center;font-size:6.6px;line-height:1.7;color:var(--text-grey)}
.why .button{position:absolute;left:298px;top:160px;width:60px;height:18px;border:1px solid var(--soft-blue);border-radius:9px;font-size:6.5px;line-height:16px;text-align:center;color:var(--mid-blue)}

/* footer */
.site-footer{position:absolute;left:0;top:1097px;width:656px;height:103px;background:#0c1d22}
.footer-contacts{position:absolute;left:0;right:0;top:18px;display:flex;justify-content:center;gap:64px}
.footer-contacts span{display:flex;align-items:center;gap:12px;color:var(--white);font-size:12px}
.diamond-icon{width:18px;height:18px;transform:rotate(45deg);background:var(--cyan);display:flex;align-items:center;justify-content:center}
.diamond-icon svg{width:11px;height:11px;transform:rotate(-45deg)}
.footer-rule{position:absolute;left:10px;right:10px;top:62px;height:1px;background:rgba(255,255,255,.12)}
.copyright{position:absolute;left:10px;top:78px;font-size:5.5px;color:#9fb0b6}
.social{position:absolute;right:10px;top:74px;display:flex;gap:6px}
.social i{width:11px;height:11px;background:var(--sky);display:block;border-radius:2px}
</style>
</head>
<body>
<div class="page">
  <div class="backdrop" role="img" aria-label="Dark teal background with faint binary digits"></div>
  <div class="panel">

    <header class="site-header">
      <div class="brand"><span class="brand-name">ByteWell</span><span class="brand-tag">Computer Services</span></div>
      <nav class="main-nav">
        <a class="active">HOME</a><a>ABOUT US</a><a>OUR SERVICES ▾</a><a>CONTACT US</a>
      </nav>
      <div class="contact-strip">
        <span><svg viewBox="0 0 10 10"><rect x="0.5" y="2" width="9" height="6" fill="none" stroke="#4fc3e8"/><path d="M0.5 2 L5 5.5 L9.5 2" fill="none" stroke="#4fc3e8"/></svg>info@company.com</span>
        <span><svg viewBox="0 0 10 10"><path d="M2 1 L4 1 L4.6 3 L3.4 4 Q4.5 6 6 6.6 L7 5.4 L9 6 L9 8 Q5 9 2 5 Q1 3 2 1Z" fill="#4fc3e8"/></svg>1234567890</span>
      </div>
    </header>

    <section class="hero" role="img" aria-label="Technician's hands repairing an open laptop with a screwdriver">
      <div class="slide-arrow prev"><svg viewBox="0 0 8 10"><path d="M6 1 L2 5 L6 9" fill="none" stroke="#fff" stroke-width="1.6"/></svg></div>
      <div class="slide-arrow next"><svg viewBox="0 0 8 10"><path d="M2 1 L6 5 L2 9" fill="none" stroke="#fff" stroke-width="1.6"/></svg></div>
      <div class="slide-dots"><i></i><i class="on"></i><i></i></div>
    </section>

    <section class="services">
      <h2 class="section-title">OUR SERVICES</h2>
      <div class="title-rule"></div>

      <div class="tile" style="left:120px;top:102px"></div>
      <div class="tile photo" style="left:276px;top:102px" role="img" aria-label="Close-up of computer hardware being serviced"></div>
      <div class="tile" style="left:432px;top:102px"></div>
      <div class="tile" style="left:198px;top:180px"></div>
      <div class="tile" style="left:354px;top:180px"></div>
      <div class="tile" style="left:276px;top:258px"></div>

      <div class="service" style="left:132px;top:121px">
        <h3>Honest Service</h3>
        <p>Our certified technicians won't push an upgrade you don't need or add unneeded services.</p>
        <span class="more">Read More</span>
      </div>
      <div class="service" style="left:444px;top:121px">
        <h3>Malware/Virus Removal</h3>
        <p>Infections can come from many places and sometimes antivirus just isn't enough.</p>
        <span class="more">Read More</span>
      </div>
      <div class="service" style="left:210px;top:199px">
        <h3>Upgrades</h3>
        <p>A new video card to play the latest game at the highest settings? A new disk to speed up?</p>
        <span class="more">Read More</span>
      </div>
      <div class="service" style="left:366px;top:199px">
        <h3>Data Rescue</h3>
        <p>Flash drive formatted? Hard drive corrupted? Data loss can be devastating.</p>
        <span class="more">Read More</span>
      </div>
      <div class="service" style="left:288px;top:277px">
        <h3>In-Home Installation</h3>
        <p>All our services come with pick up and drop off installation. You won't be left to set up wireless.</p>
        <span class="more">Read More</span>
      </div>

      <div class="view-all">View All</div>
    </section>

    <section class="why">
      <h2 class="section-title">WHY CHOOSE US</h2>
      <p>Lorem Ipsum is simply dummy text of the printing and typesetting industry. Lorem Ipsum has been the industry's standard dummy text ever since the 1500s, when an unknown printer took a galley of type and scrambled it to make a type specimen book. It has survived not only five centuries, but also the leap into electronic typesetting, remaining essentially unchanged.</p>
      <div class="button">Read More</div>
    </section>

    <footer class="site-footer">
      <div class="footer-contacts">
        <span><i class="diamond-icon"><svg viewBox="0 0 10 10"><rect x="0.5" y="2" width="9" height="6" fill="none" stroke="#fff"/><path d="M0.5 2 L5 5.5 L9.5 2" fill="none" stroke="#fff"/></svg></i>info@company.com</span>
        <span><i class="diamond-icon"><svg viewBox="0 0 10 10"><path d="M2 1 L4 1 L4.6 3 L3.4 4 Q4.5 6 6 6.6 L7 5.4 L9 6 L9 8 Q5 9 2 5 Q1 3 2 1Z" fill="#fff"/></svg></i>1234567890</span>
      </div>
      <div class="footer-rule"></div>
      <div class="copyright">© 2015. All Rights Reserved</div>
      <div class="social"><i></i><i></i><i></i><i></i><i></i></div>
    </footer>

  </div>
</div>
</body>
</html>
```